Brimsett Gardening Fresh New Website

We are looking to create a simple fresh website for our landscaping business. The website should appeal to a 'high end' audience. We deal with a lot of Embassies and affluent clients who have extremely large gardens that are meticulously maintained. The site is about communicating our excellent landscaping and customer service skills and encouraging new clients to reach out and engage us to take care of their gardens.

The website is basically going to be our business card, it will have almost no functionality other than two 'contact us' forms, one for smaller clients and one for more detailed projects.

The website will not have a lot of written content and will have to show photos of beautifully landscaped gardens.

The main logo in black will influence the site, however, we are open to all suggestions.

We are expecting to have the following pages:
Home Page
Services
About Us
Contact Us
Showcase (photo gallery of our work)

We need someone who can code it to wordpress and be available for minor changes over a number of days. They will be simple tweaks.

```html
<!DOCTYPE html>
<html lang="en">
<head>
<meta charset="utf-8">
<title>Brimsett Gardening</title>
<link rel="stylesheet" href="https://fonts.googleapis.com/css2?family=Roboto:wght@400;500;700&family=Tinos:wght@400;700&display=swap">
<style>
:root{
  --gold-dark:#b8862a;
  --gold:#d4a53a;
  --gold-light:#f3d24c;
  --ink:#1b1a18;
  --ink-deep:#121110;
  --black:#000;
  --white:#fff;
  --muted:#d8d4cc;
  --gold-grad:linear-gradient(90deg,var(--gold-dark),var(--gold-light));
}
*{margin:0;padding:0;box-sizing:border-box}
html,body{width:1200px;height:3872px;overflow:hidden}
body{background:var(--ink);font-family:"Roboto",sans-serif;color:var(--white);position:relative}
.abs{position:absolute}
.serif{font-family:"Tinos",serif}
.btn{position:absolute;display:flex;align-items:center;justify-content:center;gap:8px;border-radius:30px;background:var(--gold-grad);color:var(--white);font-weight:700;font-size:15px;text-transform:uppercase;text-decoration:none}
.btn .dot{width:14px;height:14px;border-radius:50%;background:var(--white);display:inline-flex;align-items:center;justify-content:center}
.btn .dot::after{content:"";border-left:5px solid var(--gold);border-top:3.5px solid transparent;border-bottom:3.5px solid transparent;margin-left:2px}
.eyebrow{position:absolute;left:0;width:1200px;text-align:center;color:var(--gold);font-weight:500;font-size:14px;text-transform:uppercase}
.heading{position:absolute;left:0;width:1200px;text-align:center;font-family:"Tinos",serif;font-weight:700;font-size:36px;text-transform:uppercase;color:var(--white)}
.heading .accent{color:var(--gold)}

/* header */
.topbar{left:0;top:0;width:1200px;height:122px;background:var(--ink)}
.logo-box{left:150px;top:0;width:174px;height:158px;background:var(--ink);clip-path:polygon(0 0,100% 0,100% 100%,12% 100%,0 82%)}
.brand-mark{left:219px;top:30px;width:36px;height:36px;border:2px solid var(--gold);border-radius:50%}
.brand{left:150px;top:96px;width:174px;text-align:center;font-family:"Roboto",sans-serif;color:var(--gold);font-weight:500;font-size:17px;line-height:1.2}
.contact-top{top:20px;display:flex;align-items:center;gap:14px;font-size:12px}
.contact-top b{display:block;font-size:15px;font-weight:500;margin-top:3px}
.nav{left:426px;top:80px;width:774px;height:42px;background:linear-gradient(90deg,var(--gold-dark),var(--gold) 60%,var(--gold-light));clip-path:polygon(4% 0,100% 0,100% 100%,0 100%)}
.nav a{position:absolute;top:13px;color:var(--white);text-decoration:none;font-size:14px;font-weight:500}
.nav .quote{top:0;height:42px;width:122px;left:508px;background:var(--gold-dark);display:flex;align-items:center;justify-content:center}

/* hero */
.hero-photo{left:0;top:122px;width:1200px;height:690px;background:linear-gradient(100deg,#2d3320 0%,#4a5130 35%,#6d6a48 55%,#3c5a2c 75%,#80744a 100%)}
.hero-shade{left:0;top:122px;width:700px;height:690px;background:linear-gradient(90deg,rgba(0,0,0,.55),rgba(0,0,0,0))}
.hero-title{left:140px;top:332px;font-size:40px;font-weight:400;text-transform:uppercase}
.hero-text{left:140px;top:395px;width:470px;font-size:15.5px;font-weight:500;line-height:26px}

/* about */
.about-photo{left:146px;top:894px;width:384px;height:384px;border-radius:50%;background:radial-gradient(circle at 40% 40%,#8a8272,#5f6a3e 60%,#3d4a2a)}
.about-inset{left:384px;top:1121px;width:174px;height:174px;border-radius:50%;border:8px solid var(--ink);background:radial-gradient(circle,#6f9a3a,#3e6a22)}
.about-title{left:629px;top:944px;font-size:36px;font-weight:700;text-transform:uppercase}
.about-copy{left:629px;top:1016px;width:430px;font-size:13px;line-height:23px;color:var(--muted)}
.about-copy p+p{margin-top:13px}

/* services */
.services-bg{left:0;top:1480px;width:1200px;height:560px;background:var(--ink-deep)}
.card{top:1599px;width:292px;height:367px;background:var(--black);border:2px solid #2a2824}
.card-photo{position:absolute;left:2px;top:2px;width:284px;height:213px;clip-path:polygon(0 0,100% 0,100% 100%,50% 84%,0 100%)}
.card-icon{position:absolute;left:113px;top:155px;width:66px;height:66px;border-radius:50%;background:var(--gold-grad);display:flex;align-items:center;justify-content:center}
.card h3{position:absolute;top:232px;width:100%;text-align:center;font-size:17px;font-weight:700}
.card p{position:absolute;top:264px;left:16px;right:16px;text-align:center;font-size:12.5px;line-height:22px;color:var(--muted)}
.card .more{position:absolute;top:326px;width:100%;text-align:center;color:var(--gold);font-weight:700;font-size:13px}

/* gallery */
.tile{position:absolute}

/* contact */
.info{top:3176px;display:flex;gap:16px;align-items:flex-start;font-size:12.5px;line-height:18px}
.info b{display:block;font-size:15px;text-transform:uppercase;margin-bottom:4px}
.field{position:absolute;background:var(--white);border-radius:3px;color:#888;font-size:12px;padding:14px 18px}
.submit{left:504px;top:3473px;width:192px;height:48px;background:var(--ink);display:flex;align-items:center;justify-content:center;gap:8px;font-weight:700;font-size:15px;border-radius:2px}

/* footer */
.footer-mark{left:219px;top:3690px;width:40px;height:40px;border:2px solid var(--gold);border-radius:50%}
.footer-brand{left:130px;top:3770px;width:214px;text-align:center;font-family:"Roboto",sans-serif;color:var(--gold);font-weight:500;font-size:22px}
.footer-nav{left:426px;top:3681px;display:flex;gap:26px;font-size:12.5px;font-weight:700}
.footer-nav span.sep{font-weight:400}
.copy{left:426px;top:3721px;font-size:12px}
.copy u{font-weight:500}
.social{top:3770px;width:40px;height:40px;border-radius:50%;background:var(--white)}
</style>
</head>
<body>

<!-- HERO -->
<div class="abs hero-photo" role="img" aria-label="Gardeners planting young plants in a garden bed"></div>
<div class="abs hero-shade"></div>
<h1 class="abs hero-title serif">Brimsett Gardening</h1>
<p class="abs hero-text">Lorem ipsum dolor sit amet, consectetur adipiscing elit, sed do incididunt ut labore et dolore magna aliqua.</p>
<a class="btn" style="left:141px;top:474px;width:191px;height:48px">Get Started <span class="dot"></span></a>
<svg class="abs" style="left:0;top:600px" width="1200" height="220" viewBox="0 600 1200 220">
  <defs><linearGradient id="g1" x1="0" x2="1"><stop offset="0" stop-color="#b8862a"/><stop offset="1" stop-color="#f3d24c"/></linearGradient></defs>
  <path d="M0,665 Q520,880 1000,700 L1200,640 L1200,820 L0,820 Z" fill="#1b1a18"/>
  <path d="M0,640 Q520,850 1000,702 Q560,900 0,672 Z" fill="url(#g1)"/>
</svg>

<!-- HEADER -->
<div class="abs topbar"></div>
<div class="abs logo-box"></div>
<div class="abs brand-mark"></div>
<div class="abs brand">Brimsett Gardening</div>
<div class="abs contact-top" style="left:634px">
  <svg width="30" height="22" viewBox="0 0 30 22"><rect x="1" y="1" width="28" height="20" fill="none" stroke="#d4a53a" stroke-width="2"/><path d="M1 1 L15 12 L29 1" fill="none" stroke="#d4a53a" stroke-width="2"/></svg>
  <div>Email<b>hello@brimsettgardens.net</b></div>
</div>
<div class="abs contact-top" style="left:886px">
  <svg width="34" height="34" viewBox="0 0 34 34"><circle cx="17" cy="17" r="15" fill="none" stroke="#d4a53a" stroke-width="2"/><path d="M11 10 q-2 8 12 14 l2-3 -4-3 -2 2 q-4-2-6-6 l2-2 -3-4 z" fill="#d4a53a"/></svg>
  <div>Call Us:<b>+1 555 014 2380</b></div>
</div>
<nav class="abs nav">
  <a style="left:40px">Home</a>
  <a style="left:111px">About Us</a>
  <a style="left:203px">Our Services</a>
  <a style="left:317px">Our Work</a>
  <a style="left:405px">Contact Us</a>
  <a class="quote">Get A Quote</a>
</nav>

<!-- ABOUT -->
<div class="abs about-photo" role="img" aria-label="Landscaper laying turf beside a paved path"></div>
<div class="abs about-inset" role="img" aria-label="Aerial view of a winding garden path through lawn"></div>
<div class="abs" style="left:629px;top:920px;color:var(--gold);font-weight:500;font-size:14px">WELCOME TO</div>
<h2 class="abs about-title serif"><span style="color:var(--gold)">Brimsett</span> Gardening</h2>
<div class="abs about-copy">
  <p>Northgate Heating and Air has seen how some companies cut corners in their service and maintenance contracts. This just didn't sit well with us, so when we saw the opportunity to provide homes and businesses with the kind of heating and air conditioning service they need and deserve, we took it, and here we are today.</p>
  <p>Northgate Heating and Air was established to meet a specific need. In our many decades in the home improvement industry</p>
</div>
<a class="btn" style="left:629px;top:1224px;width:156px;height:42px;font-size:14px">Read More <span class="dot"></span></a>

<!-- SERVICES -->
<div class="abs services-bg"></div>
<svg class="abs" style="left:0;top:1370px" width="1200" height="180" viewBox="0 1370 1200 180">
  <path d="M0,1550 L0,1480 Q600,1330 1200,1500 L1200,1550 Z" fill="#121110"/>
  <path d="M205,1480 Q700,1310 1200,1505 L1200,1550 Q700,1360 205,1480 Z" fill="url(#g1)"/>
</svg>
<div class="eyebrow" style="top:1493px">What We Do</div>
<h2 class="heading" style="top:1518px"><span class="accent">Our</span> Services</h2>

<div class="abs card" style="left:143px">
  <div class="card-photo" role="img" aria-label="Workers rolling out fresh turf" style="background:linear-gradient(160deg,#7a8a5a,#5a4a30)"></div>
  <div class="card-icon"><svg width="34" height="24" viewBox="0 0 34 24"><rect x="3" y="3" width="28" height="18" fill="none" stroke="#fff" stroke-width="2"/><path d="M12 3v18M22 3v18" stroke="#fff" stroke-width="2"/></svg></div>
  <h3>Residential</h3>
  <p>Lorem ipsum dolor sit amet, consectetur adipiscing elit, sed do eiusmod</p>
  <div class="more">READ MORE ➔</div>
</div>
<div class="abs card" style="left:454px">
  <div class="card-photo" role="img" aria-label="Gardener tending a flower bed" style="background:linear-gradient(160deg,#5f8a3a,#3e5a26)"></div>
  <div class="card-icon"><svg width="34" height="24" viewBox="0 0 34 24"><rect x="3" y="3" width="28" height="18" fill="none" stroke="#fff" stroke-width="2"/><path d="M12 3v18M22 3v18" stroke="#fff" stroke-width="2"/></svg></div>
  <h3>Commercial</h3>
  <p>Lorem ipsum dolor sit amet, consectetur adipiscing elit, sed do eiusmod</p>
  <div class="more">READ MORE ➔</div>
</div>
<div class="abs card" style="left:766px">
  <div class="card-photo" role="img" aria-label="Gardener holding pruning shears among shrubs" style="background:linear-gradient(160deg,#4f7a30,#7a4a3a)"></div>
  <div class="card-icon"><svg width="34" height="24" viewBox="0 0 34 24"><rect x="3" y="3" width="28" height="18" fill="none" stroke="#fff" stroke-width="2"/><path d="M12 3v18M22 3v18" stroke="#fff" stroke-width="2"/></svg></div>
  <h3>Service and Maintenance</h3>
  <p>Lorem ipsum dolor sit amet, consectetur adipiscing elit, sed do eiusmod</p>
  <div class="more">READ MORE ➔</div>
</div>

<svg class="abs" style="left:0;top:1960px" width="1200" height="190" viewBox="0 1960 1200 190">
  <path d="M0,1990 L0,2040 Q520,2180 1000,2045 L1200,2000 L1200,1960 L0,1960 Z" fill="#121110"/>
  <path d="M0,1978 Q500,2180 1000,2045 Q520,2210 0,2010 Z" fill="url(#g1)"/>
</svg>

<!-- GALLERY -->
<div class="eyebrow" style="top:2214px">Gallery</div>
<h2 class="heading" style="top:2238px"><span class="accent">Our</span> Work</h2>
<div class="tile" style="left:143px;top:2316px;width:453px;height:262px;background:linear-gradient(150deg,#4e6a34,#6f8a3e 50%,#3a3a2a)" role="img" aria-label="Hosta border with a wheelbarrow on a lawn"></div>
<div class="tile" style="left:603px;top:2316px;width:453px;height:262px;background:linear-gradient(150deg,#6a7a4a,#8a7a5a 45%,#4a7a2a)" role="img" aria-label="Curved stone retaining wall with planted terraces"></div>
<div class="tile" style="left:143px;top:2588px;width:301px;height:238px;background:linear-gradient(150deg,#4a3a2a,#5a7a34)" role="img" aria-label="Landscaper laying turf around a circular bed"></div>
<div class="tile" style="left:454px;top:2588px;width:291px;height:238px;background:linear-gradient(160deg,#1e2a16,#4a5a26 60%,#6a5a2a)" role="img" aria-label="Evening garden lit by path lights"></div>
<div class="tile" style="left:755px;top:2588px;width:301px;height:238px;background:linear-gradient(150deg,#5a8a2a,#7aa03a 50%,#8a8a80)" role="img" aria-label="Lawn with stepping stones and a paved path"></div>
<a class="btn" style="left:510px;top:2876px;width:180px;height:45px;font-size:14px">View All Work <span class="dot"></span></a>

<!-- CONTACT -->
<svg class="abs" style="left:0;top:2990px" width="1200" height="660" viewBox="0 2990 1200 660">
  <path d="M0,3100 Q600,2920 1200,3060 L1200,3560 Q600,3700 0,3540 Z" fill="url(#g1)"/>
  <path d="M0,3060 Q600,2900 1200,3020 L1200,3040 Q600,2935 0,3085 Z" fill="url(#g1)"/>
  <path d="M250,3560 Q700,3600 1200,3480 L1200,3510 Q700,3620 250,3560 Z" fill="#1b1a18"/>
  <path d="M0,3545 Q600,3720 1200,3555 L1200,3650 L0,3650 Z" fill="#1b1a18"/>
  <path d="M250,3585 Q650,3660 1050,3590 Q650,3640 250,3585 Z" fill="url(#g1)"/>
</svg>
<div class="eyebrow" style="top:3084px;color:var(--white)">Contact Us</div>
<h2 class="heading" style="top:3108px">Get A Quote</h2>

<div class="abs info" style="left:221px">
  <svg width="46" height="46" viewBox="0 0 46 46"><path d="M23 4a10 10 0 0 1 10 10c0 8-10 18-10 18S13 22 13 14A10 10 0 0 1 23 4z" fill="none" stroke="#fff" stroke-width="2"/><circle cx="23" cy="14" r="4" fill="none" stroke="#fff" stroke-width="2"/><path d="M8 42l6-10h18l6 10z" fill="none" stroke="#fff" stroke-width="2"/></svg>
  <div><b>Address:</b>27 Alder Row, Suite 4, Fairmont,<br>NY 10099</div>
</div>
<div class="abs info" style="left:543px">
  <svg width="46" height="46" viewBox="0 0 46 46"><path d="M10 6l8 2 2 9-5 3q4 8 11 11l3-5 9 2 2 8q-4 5-10 3Q10 34 6 16q-1-7 4-10z" fill="none" stroke="#fff" stroke-width="2"/></svg>
  <div><b>Phone:</b>+1 555 014 2380</div>
</div>
<div class="abs info" style="left:752px">
  <svg width="50" height="40" viewBox="0 0 50 40"><rect x="2" y="4" width="46" height="32" fill="none" stroke="#fff" stroke-width="2"/><path d="M2 4l23 18L48 4M2 36l17-15M48 36L31 21" fill="none" stroke="#fff" stroke-width="2"/></svg>
  <div><b>E-mail:</b>hello@brimsettgardens.net</div>
</div>

<div class="field" style="left:185px;top:3267px;width:402px;height:46px">Name</div>
<div class="field" style="left:185px;top:3328px;width:402px;height:48px">Email Address</div>
<div class="field" style="left:185px;top:3390px;width:402px;height:47px">Phone Number</div>
<div class="field" style="left:609px;top:3265px;width:406px;height:175px">Message</div>
<div class="abs submit">SUBMIT NOW <span style="width:14px;height:14px;border-radius:50%;background:#fff;display:inline-block"></span></div>

<!-- FOOTER -->
<div class="abs footer-mark"></div>
<div class="abs footer-brand">Brimsett Gardening</div>
<div class="abs footer-nav">
  <span>HOME</span><span class="sep">/</span><span>ABOUT</span><span class="sep">/</span><span>OUR SERVICES</span><span class="sep">/</span><span>OUR WORK</span><span class="sep">/</span><span>CONTACT US</span>
</div>
<div class="abs copy">Copyright© 2024 <u>Brimsett Gardening</u> | All Rights Reserved</div>
<div class="abs social" style="left:425px;background:var(--gold-grad)" aria-label="Social link"></div>
<div class="abs social" style="left:473px" aria-label="Social link"></div>
<div class="abs social" style="left:521px" aria-label="Social link"></div>
<div class="abs social" style="left:570px" aria-label="Social link"></div>

</body>
</html>
```